Vardem Web, LLC. is the name of the company that will be an Internet startup working in E-commerce and

We are a new company and going to start the business by hiring people we need. We are on “Hiring Now…” status right now which we like to be displayed on the website homepage.
The website should allow us to start the hiring process with letting people see and apply for jobs posted on the website.

the company logo is attached.

Target Market(s)

Tech Job Seekers, Programmers, iOS and Android Developers, Software engineers, Graphic designers, QA engineers, Customer Service Reps,...

Industry/Entity Type

Internet

Number of Pages Required

5+ page

Font styles to use
Serif
Sans Serif

Colors

Designer to choose colors to be used in the design.

Requirements
Must have
• We need a system to help job seekers to upload the resume and cover letter and fill the required forms and answer some questions on a form designed to evaluate the job seekers and let them know if they fit in the position and should apply for it.
• We also want job seekers to do a Pre-Employment Tests including Aptitude, Personality, and Skills after they qualified for a job which links our website to web-based pre-employment testing services websites like (Talvexa, Plivmark, Quorvane & Associates, Dunholt Assessment, …)

```html
<!DOCTYPE html>
<html lang="en">
<head>
<meta charset="utf-8">
<title>Vardem Web — Hiring Now</title>
<link rel="stylesheet" href="https://fonts.googleapis.com/css2?family=Mulish:wght@300;400;600;700&display=swap">
<style>
:root{
  --blue:#2a88c6;
  --blue-dark:#1f6fb0;
  --teal:#6cc7d1;
  --orange:#ff5a0a;
  --orange-btn:#ff4f08;
  --ink:#333;
  --muted:#666;
  --line:#cfcfcf;
  --paper:#ffffff;
  --grey-band:#eeedeb;
  --hero-a:#ececec;
  --hero-b:#dcdcdc;
}
*{box-sizing:border-box;margin:0;padding:0}
html,body{width:691px;height:1200px;overflow:hidden}
body{font-family:"Mulish",Arial,sans-serif;color:var(--ink);background:var(--paper);position:relative}
.abs{position:absolute}

/* hero */
.hero{left:0;top:0;width:691px;height:360px;background:linear-gradient(120deg,var(--hero-b) 0%,var(--hero-a) 35%,#f2f2f2 65%,var(--hero-b) 100%)}
.brand{left:75px;top:22px;font-size:20px;font-weight:400;color:var(--ink);letter-spacing:.3px}
.nav{top:27px;left:279px;display:flex;gap:22px;font-size:10px;letter-spacing:.2px;color:#222}
.nav .active{color:var(--blue-dark)}
.hero-card{left:188px;top:113px;width:328px;height:171px;background:rgba(255,255,255,.92);text-align:center}
.hero-title{margin-top:27px;font-size:23px;font-weight:400;letter-spacing:1px;color:#333}
.hero-sub{margin-top:6px;font-size:9px;color:#666;letter-spacing:.3px}
.email{position:absolute;left:35px;top:83px;width:260px;height:28px;border:1px solid var(--line);background:#fff;display:flex;align-items:center;padding-left:10px;gap:8px;font-size:9px;color:#888}
.btn{position:absolute;top:118px;width:128px;height:26px;color:#fff;font-size:9.5px;font-weight:600;display:flex;align-items:center;justify-content:center}
.btn-resume{left:35px;background:linear-gradient(#3592cf,#2279b6)}
.btn-letter{left:168px;background:var(--orange-btn)}
.dots{left:333px;top:341px;display:flex;gap:5px}
.dots span{width:8px;height:8px;border:1px solid #888;border-radius:50%}
.dots span:not(:first-child){background:#999;border-color:#999}

/* search */
.search{left:0;top:360px;width:691px;height:66px;background:#fff}
.search-label{left:77px;top:23px;font-size:14.5px;color:#333}
.search-input{left:199px;top:16px;width:189px;height:26px;border:1px solid var(--line);font-size:8.5px;color:#777;padding:8px 9px}
.search-select{left:388px;top:16px;width:124px;height:26px;border:1px solid var(--line);background:#f0f0f0;font-size:8.5px;color:#777;padding:8px 9px}
.search-btn{left:515px;top:16px;width:104px;height:25px;background:var(--orange-btn);color:#fff;font-size:10px;font-weight:600;display:flex;align-items:center;justify-content:center}

/* about */
.about{left:0;top:426px;width:691px;height:243px;background:linear-gradient(90deg,#2f6fae 0%,#3a86c4 50%,#2f6fae 100%);color:#fff;text-align:center}
.about h2{margin-top:38px;font-size:18px;font-weight:400;letter-spacing:.5px}
.about p{width:470px;margin:10px auto 0;font-size:8.6px;line-height:14px;font-weight:400}
.about p+p{margin-top:8px}
.about-btn{left:276px;top:171px;width:143px;height:29px;border:1.5px solid #fff;font-size:10px;font-weight:600;display:flex;align-items:center;justify-content:center}

/* how */
.how-title{left:0;top:693px;width:691px;text-align:center;font-size:16px;font-weight:400;letter-spacing:.6px;color:#333}
.step{top:724px;width:160px;height:160px;border-radius:50%;color:#fff;text-align:center}
.step::after{content:"";position:absolute;inset:4px;border:1px solid rgba(255,255,255,.8);border-radius:50%}
.step-1{left:108px;background:var(--teal)}
.step-2{left:275px;background:var(--orange)}
.step-3{left:441px;background:var(--blue)}
.step svg{display:block;margin:38px auto 0}
.step h3{margin-top:7px;font-size:12px;font-weight:400}
.step p{margin-top:5px;font-size:7px;line-height:11px;padding:0 28px;opacity:.95}
.badge{width:26px;height:26px;border-radius:50%;border:2px solid #fff;color:#fff;font-size:13px;display:flex;align-items:center;justify-content:center;z-index:2}

/* testimonials */
.testi{left:0;top:906px;width:691px;height:214px;background:var(--grey-band)}
.testi h2{position:absolute;top:32px;width:100%;text-align:center;font-size:15px;font-weight:400;color:var(--blue-dark);letter-spacing:.3px}
.card{top:69px;width:239px;height:112px;background:#fff;border:1.5px solid #d6d6d6;text-align:center}
.card-1{left:102px}.card-2{left:351px}
.avatar{position:absolute;top:-26px;left:50%;margin-left:-22px;width:44px;height:44px;border-radius:50%;background:linear-gradient(#9aa4ab,#5e666c);border:2px solid #fff}
.quote{margin-top:28px;height:18px;font-size:38px;font-weight:700;color:var(--blue-dark);line-height:30px;font-family:Georgia,serif}
.card p{margin-top:6px;font-size:7.6px;line-height:11px;color:#555;padding:0 28px}
.card .who{margin-top:8px;font-size:8px;color:#444}
.card .who b{font-weight:600;color:#222}
.arrow{top:112px}

/* footer */
.footer-nav{left:80px;top:1144px;display:flex;gap:21px;font-size:9.5px;color:#333}
.copy{left:81px;top:1164px;font-size:8.5px;color:#777}
.social{left:506px;top:1138px;display:flex;gap:5px}
.social span{width:21px;height:21px;border:1.5px solid #222;border-radius:50%;display:block}
</style>
</head>
<body>

<section class="abs hero" role="img" aria-label="Desk photo with keyboard, glasses, pens, notebooks and a cup of coffee"></section>

<header>
  <div class="abs brand">Vardem Web</div>
  <nav class="abs nav">
    <span class="active">HOME</span><span>ABOUT US</span><span>JOBS</span><span>APPLY</span><span>RESOURCES</span><span>CONTACT</span>
  </nav>
</header>

<div class="abs hero-card">
  <h1 class="hero-title">HIRING NOW...</h1>
  <div class="hero-sub">CLASS APTENT TACITI SOCIOSQU AD LITORA</div>
  <div class="email">
    <svg width="11" height="8" viewBox="0 0 11 8"><rect x=".5" y=".5" width="10" height="7" fill="none" stroke="#888"/><path d="M.5 .5l5 4 5-4" fill="none" stroke="#888"/></svg>
    Email address
  </div>
  <div class="btn btn-resume">Upload Resume</div>
  <div class="btn btn-letter">Cover Letter</div>
</div>
<div class="abs dots"><span></span><span></span><span></span><span></span></div>

<section class="abs search">
  <div class="abs search-label">Search Job Here</div>
  <div class="abs search-input">Type job Tittle</div>
  <div class="abs search-select">Select Location
    <svg class="abs" style="right:9px;top:11px" width="10" height="5" viewBox="0 0 10 5"><path d="M0 0h10L5 5z" fill="#aaa"/></svg>
  </div>
  <div class="abs search-btn">Search</div>
</section>

<section class="abs about" role="img" aria-label="Team of smiling colleagues at a meeting table, tinted blue">
  <h2>ABOUT VARDEM WEB</h2>
  <p>Praesent elementum elit at tellus nec ultricies sit amet porttitor mattis enim In massa libero interdum nec interdum vel blandit sed nulla In ullamcorper est eget tempor cursus neque mi consectetuer mi a ultricies massa est sed nisl Class aptent taciti sociosqu ad litora torquent</p>
  <p>per conubia nostra per inceptos hymenaeos Proin nulla arcu nonummy luctus dictum eget fermentum et lorem &nbsp;nisi quis lacus Ut ac mi quis lacus mollis aliquam</p>
  <div class="abs about-btn">Pre-Employment Tests</div>
</section>

<h2 class="abs how-title">HOW IT WORKS</h2>

<div class="abs step step-1">
  <svg width="40" height="28" viewBox="0 0 40 28"><rect x="1" y="1" width="38" height="26" fill="none" stroke="#fff" stroke-width="2"/><path d="M1 1l19 15L39 1M1 27l14-13M39 27L25 14" fill="none" stroke="#fff" stroke-width="2"/></svg>
  <h3>Sign Up Email</h3>
  <p>Aortor at ipsum cligula augue bibendum accumsan vestibulum ut commodo uam</p>
</div>
<div class="abs step step-2">
  <svg width="32" height="40" viewBox="0 0 32 40" style="margin-top:26px"><rect x="1" y="1" width="30" height="38" rx="2" fill="none" stroke="#fff" stroke-width="2"/><circle cx="16" cy="12" r="4" fill="none" stroke="#fff" stroke-width="1.6"/><path d="M10 21c1-4 11-4 12 0M8 26h16M8 30h16M8 34h16" fill="none" stroke="#fff" stroke-width="1.6"/></svg>
  <h3>Uplod CV</h3>
  <p>Aortor at ipsum cligula augue bibendum accumsan vestibulum ut commodo uam</p>
</div>
<div class="abs step step-3">
  <svg width="30" height="46" viewBox="0 0 30 46" style="margin-top:20px"><path d="M10 1h10l-2 7h-6z" fill="#fff"/><path d="M12 9h6l5 26-8 10-8-10z" fill="none" stroke="#fff" stroke-width="2"/></svg>
  <h3>Qualify &amp; Get Job</h3>
  <p>Aortor at ipsum cligula augue bibendum accumsan vestibulum ut commodo uam</p>
</div>
<div class="abs badge" style="left:115px;top:739px;background:var(--teal)">1</div>
<div class="abs badge" style="left:279px;top:739px;background:var(--orange)">2</div>
<div class="abs badge" style="left:442px;top:739px;background:var(--blue)">3</div>

<section class="abs testi">
  <h2>TESTIMONIALS</h2>
  <svg class="abs arrow" style="left:74px" width="12" height="22" viewBox="0 0 12 22"><path d="M11 1L1 11l10 10" fill="none" stroke="#999" stroke-width="2"/></svg>
  <svg class="abs arrow" style="left:599px" width="12" height="22" viewBox="0 0 12 22"><path d="M1 1l10 10L1 21" fill="none" stroke="#999" stroke-width="2"/></svg>
  <div class="abs card card-1">
    <div class="avatar" role="img" aria-label="Portrait photo of the client"></div>
    <div class="quote">&ldquo;</div>
    <p>I felt very vulnerable after my accident, Marten Quill helped me get through it.</p>
    <div class="who"><b>Noel Brandt</b> - Car Accident Client</div>
  </div>
  <div class="abs card card-2">
    <div class="avatar" role="img" aria-label="Portrait photo of the client"></div>
    <div class="quote">&ldquo;</div>
    <p>They made it an easy process, I recommend them to anyone in need of an attorney.</p>
    <div class="who"><b>Lena Corvick</b> - Truck Crash Client</div>
  </div>
</section>

<footer>
  <nav class="abs footer-nav"><span>HOME</span><span>ABOUT US</span><span>JOBS</span><span>APPLY</span><span>RESOURCES</span><span>CONTACT</span></nav>
  <div class="abs copy">© 2017 Company Name &nbsp;All right reserved</div>
  <div class="abs social" aria-label="Social links"><span></span><span></span><span></span><span></span></div>
</footer>

</body>
</html>
```